Business cards to launch an education platform

Hi,
I am looking at having new business cards designed.
I am a startup, developing a web platform for schools and university, the education world. It's an online assessment system.
I would like a card that looks classy, and that is using the colors and the font of my logo.

I have attached:
1) my logo
2) A business card that I have designed quickly so you can have all the information required in the card, but I really don't like it.
3) The font that I am using (Lato Regular) to design my web platform
4) Some screenshots of my web platform so you can have a look at the style that I have.

Target Market(s)

Major market: Education system: Schools and university
Minor markets: Business in general

Industry/Entity Type

Business

Contact Information for Business Card

Clara Fenwick
Director

M: 0437 518 902
E: clara.fenwick@amberLoomSystems.com.au

Requirements
Must have
• The colors of my logo

```html
<!DOCTYPE html>
<html lang="en">
<head>
<meta charset="utf-8">
<title>Amber Loom Systems — Business Cards</title>
<link href="https://fonts.googleapis.com/css2?family=Lato:wght@400&display=swap" rel="stylesheet">
<style>
  :root {
    --backdrop: #3a3431;
    --card: #0d0d0e;
    --brand-blue: #1f8fd6;
    --accent-cyan: #2bc3ee;
    --text-light: #f2f4f6;
  }
  * { margin: 0; padding: 0; box-sizing: border-box; }
  html, body {
    width: 1200px;
    height: 844px;
    overflow: hidden;
    background: var(--backdrop);
    font-family: "Lato", sans-serif;
  }
  .card-set {
    position: absolute;
    inset: 0;
    display: flex;
    align-items: center;
    justify-content: center;
    gap: 40px;
  }
  .card {
    position: relative;
    width: 540px;
    height: 330px;
    background: var(--card);
    border-radius: 4px;
    box-shadow: 0 10px 30px rgba(0,0,0,0.45);
  }
  .brand {
    position: absolute;
    display: flex;
    align-items: center;
    gap: 16px;
    color: var(--brand-blue);
    font-weight: 400;
  }
  .brand-square {
    width: 64px;
    height: 64px;
    background: var(--brand-blue);
    flex: none;
  }
  .brand-name {
    font-size: 26px;
    line-height: 1.1;
    letter-spacing: 2px;
  }
  .card--front .brand { left: 44px; top: 72px; }
  .card--back .brand { left: 50%; top: 50%; transform: translate(-50%, -50%); }

  .contact {
    position: absolute;
    right: 30px;
    color: var(--text-light);
    font-size: 13px;
    display: flex;
    align-items: center;
    gap: 8px;
  }
  .contact svg { width: 12px; height: 12px; fill: var(--accent-cyan); flex: none; }
  .contact--phone { top: 152px; }
  .contact--email { top: 176px; }

  .person {
    position: absolute;
    left: 36px;
    bottom: 40px;
  }
  .person-name {
    color: var(--accent-cyan);
    font-size: 21px;
    margin-bottom: 4px;
  }
  .person-role {
    color: var(--text-light);
    font-size: 14px;
  }
</style>
</head>
<body>
  <main class="card-set">
    <section class="card card--front" aria-label="Business card front">
      <div class="brand">
        <span class="brand-square"></span>
        <span class="brand-name">AMBER LOOM<br>Systems</span>
      </div>

      <p class="contact contact--phone">
        0437 518 902
        <svg viewBox="0 0 24 24" aria-hidden="true"><path d="M6.6 10.8a15 15 0 0 0 6.6 6.6l2.2-2.2c.3-.3.7-.4 1-.2 1.1.4 2.3.6 3.6.6.6 0 1 .4 1 1V20c0 .6-.4 1-1 1A17 17 0 0 1 3 4c0-.6.4-1 1-1h3.5c.6 0 1 .4 1 1 0 1.3.2 2.5.6 3.6.1.3 0 .7-.2 1z"/></svg>
      </p>
      <p class="contact contact--email">
        clara.fenwick@amberLoomSystems.com.au
        <svg viewBox="0 0 24 24" aria-hidden="true"><path d="M2 5h20v14H2zm2 2v.5l8 5 8-5V7z"/></svg>
      </p>

      <div class="person">
        <p class="person-name">Clara Fenwick</p>
        <p class="person-role">Director</p>
      </div>
    </section>

    <section class="card card--back" aria-label="Business card back">
      <div class="brand">
        <span class="brand-square"></span>
        <span class="brand-name">AMBER LOOM<br>Systems</span>
      </div>
    </section>
  </main>
</body>
</html>
```